4th Generation Family Business Needs a New Card Design!

We are a family owned 4th Generation company. We are based in the Sydney, Australia area and we are desperately in need of a more modern and classy card. We are monumental masons who design, supply & erect lasting memorials throughout cemeteries in Sydney. Our customers are normally in a period of grieving. I have attached logo files that will need to be implemented on the card. Company was established 1935. Australian Owned and Operated. Card needs to be designed to PIXO.com specification.

Target Market(s)

Our target market is based upon people that a grieving for family members that have passed away. We also deal with alot of companies that own and operate cemeteries.

Industry/Entity Type

Business

Contact Information for Business Card

Simon Harcourt, Operations Manager, 0417293086, simon@harcourtmemorials.com.au
Lewis Harcourt, Director, 0491630572, lewis@harcourtmemorials.com.au
Phone # 02 9561 3048
Website: www.harcourtmemorials.com.au
Address: Suite 17, 8 Palfrey Lane, West Carlow, Sydney NSW 2156

Font styles to use
Serif
Decorative
Script

Requirements
Must have
• Would like to see the logo nicely implemented with a modern design. Embossed lettering would be a nice additive.

```html
<!DOCTYPE html>
<html lang="en">
<head>
<meta charset="utf-8">
<title>Harcourt Memorials – Business Card</title>
<link href="https://fonts.googleapis.com/css2?family=Source+Sans+3:wght@400;600&display=swap" rel="stylesheet">
<style>
  :root {
    --gold: #ebc02e;
    --gold-deep: #e0b526;
    --ink: #222222;
    --paper: #ffffff;
    --backdrop-top: #2a2a2a;
    --backdrop-bottom: #050505;
  }
  * { box-sizing: border-box; margin: 0; padding: 0; }
  html, body { width: 1200px; height: 900px; overflow: hidden; }
  body {
    position: relative;
    background: linear-gradient(180deg, var(--backdrop-top) 0%, #151515 60%, var(--backdrop-bottom) 100%);
    font-family: "Source Sans 3", "Myriad Pro", sans-serif;
  }
  .card {
    position: absolute;
    top: 170px;
    width: 347px;
    height: 561px;
    box-shadow: 0 4px 14px rgba(0,0,0,.55);
    overflow: hidden;
    text-align: center;
  }
  .card-front { left: 259px; background: var(--paper); }
  .card-back { left: 631px; background: var(--gold); color: var(--paper); }

  .tab { position: absolute; left: 115px; width: 117px; }
  .tab-top { top: 0; height: 31px; }
  .tab-bottom { bottom: 0; height: 28px; background: var(--gold); }

  .brand {
    position: absolute;
    left: 0; right: 0;
    font-weight: 600;
    letter-spacing: 2px;
    line-height: 1.1;
  }
  .card-front .brand { top: 360px - 170px; top: 190px; color: var(--ink); font-size: 40px; }
  .card-back .brand { top: 220px; color: var(--paper); font-size: 40px; }
  .brand span { display: block; font-size: 22px; letter-spacing: 4px; }

  .contacts { position: absolute; top: 318px; left: 0; right: 0; color: var(--ink); }
  .person + .person { margin-top: 8px; }
  .person-name { color: var(--gold); font-weight: 600; font-size: 19px; line-height: 24px; }
  .person-role { font-size: 15px; line-height: 20px; margin-bottom: 6px; }
  .line { font-size: 15px; line-height: 20px; }
  .line b { color: var(--gold); font-weight: 600; margin-right: 4px; }

  .back-details { position: absolute; top: 406px; left: 0; right: 0; font-size: 15px; line-height: 20px; }
  .back-details .line { display: flex; justify-content: center; align-items: center; gap: 7px; }
  .back-details svg { width: 11px; height: 11px; fill: var(--paper); }
  .address { margin-top: 29px; }
</style>
</head>
<body>
  <section class="card card-front">
    <svg class="tab tab-top" viewBox="0 0 117 31" aria-hidden="true">
      <path d="M0 0H117V31Q58.5 14 0 31Z" fill="var(--gold)"/>
    </svg>
    <div class="brand">HARCOURT<span>MEMORIALS</span></div>
    <div class="contacts">
      <div class="person">
        <div class="person-name">Simon Harcourt</div>
        <div class="person-role">Operations Manager</div>
        <div class="line"><b>P:</b>0417293086</div>
        <div class="line"><b>E:</b>simon@harcourtmemorials.com.au</div>
      </div>
      <div class="person">
        <div class="person-name">Lewis Harcourt</div>
        <div class="person-role">Director</div>
        <div class="line"><b>P:</b>0491630572</div>
        <div class="line"><b>E:</b>lewis@harcourtmemorials.com.au</div>
      </div>
    </div>
    <div class="tab tab-bottom"></div>
  </section>

  <section class="card card-back">
    <div class="brand">HARCOURT<span>MEMORIALS</span></div>
    <div class="back-details">
      <div class="line">
        <svg viewBox="0 0 24 24" aria-hidden="true"><path d="M6.6 10.8a15.1 15.1 0 0 0 6.6 6.6l2.2-2.2a1 1 0 0 1 1-.25 11.4 11.4 0 0 0 3.6.57 1 1 0 0 1 1 1V20a1 1 0 0 1-1 1A17 17 0 0 1 3 4a1 1 0 0 1 1-1h3.5a1 1 0 0 1 1 1c0 1.25.2 2.45.57 3.57a1 1 0 0 1-.25 1z"/></svg>
        <span>02 9561 3048</span>
      </div>
      <div class="line">
        <svg viewBox="0 0 24 24" aria-hidden="true"><circle cx="12" cy="12" r="11"/></svg>
        <span>www.harcourtmemorials.com.au</span>
      </div>
      <div class="address">Suite 17, 8 Palfrey Lane, West Carlow,<br>Sydney NSW 2156</div>
    </div>
  </section>
</body>
</html>
```